4th Generation Family Business Needs a New Card Design!

We are a family owned 4th Generation company. We are based in the Sydney, Australia area and we are desperately in need of a more modern and classy card. We are monumental masons who design, supply & erect lasting memorials throughout cemeteries in Sydney. Our customers are normally in a period of grieving. I have attached logo files that will need to be implemented on the card. Company was established 1935. Australian Owned and Operated. Card needs to be designed to PIXO.com specification.

Target Market(s)

Our target market is based upon people that a grieving for family members that have passed away. We also deal with alot of companies that own and operate cemeteries.

Industry/Entity Type

Business

Contact Information for Business Card

Simon Harcourt, Operations Manager, 0417293086, simon@harcourtmemorials.com.au
Lewis Harcourt, Director, 0491630572, lewis@harcourtmemorials.com.au
Phone # 02 9561 3048
Website: www.harcourtmemorials.com.au
Address: Suite 17, 8 Palfrey Lane, West Carlow, Sydney NSW 2156

Font styles to use
Serif
Decorative
Script

Requirements
Must have
• Would like to see the logo nicely implemented with a modern design. Embossed lettering would be a nice additive.

```html
<!DOCTYPE html>
<html lang="en">
<head>
<meta charset="utf-8">
<title>Harcourt Memorials — Business Card</title>
<link href="https://fonts.googleapis.com/css2?family=Lato:wght@400;700&display=swap" rel="stylesheet">
<style>
  :root {
    --page: #ececea;
    --card-white: #ffffff;
    --card-dark: #252323;
    --gold: #e9bd2c;
    --ink: #1f1d1d;
    --grey: #7d7d7d;
    --rule: #bdbdbd;
    --light: #f4f4f4;
  }
  * { box-sizing: border-box; margin: 0; padding: 0; }
  html, body { width: 1200px; height: 960px; overflow: hidden; }
  body { background: var(--page); font-family: "Lato", sans-serif; position: relative; }

  .card { position: absolute; left: 220px; width: 760px; height: 430px; box-shadow: 0 4px 12px rgba(0,0,0,.18); }
  .card--front { top: 40px; background: var(--card-white); }
  .card--back { top: 500px; background: var(--card-dark); }

  .brand-mark { position: absolute; display: flex; align-items: center; gap: 14px; font-weight: 700; letter-spacing: 3px; text-transform: uppercase; }
  .brand-mark__square { width: 18px; height: 18px; background: var(--gold); flex: none; }
  .card--front .brand-mark { left: 70px; top: 150px; width: 270px; color: var(--ink); font-size: 27px; line-height: 1.25; }
  .card--back .brand-mark { left: 0; right: 0; top: 168px; justify-content: center; color: var(--light); font-size: 38px; }

  .divider { position: absolute; left: 380px; top: 68px; width: 2px; height: 238px; background: var(--rule); }

  .contacts { position: absolute; left: 422px; top: 62px; }
  .person + .person { margin-top: 22px; }
  .person__name { color: var(--gold); font-weight: 700; font-size: 25px; letter-spacing: 1px; line-height: 1.1; }
  .person__role { color: var(--grey); font-size: 19px; letter-spacing: 1.4px; margin-top: 2px; }
  .person__lines { list-style: none; margin-top: 16px; }
  .person__line { display: flex; align-items: center; gap: 9px; color: var(--grey); font-size: 17px; line-height: 25px; }
  .person__line svg { width: 17px; height: 17px; flex: none; }

  .info-band { position: absolute; left: 0; bottom: 0; width: 100%; height: 70px; background: var(--card-dark); border-top: 4px solid var(--gold); color: var(--light); text-align: center; font-size: 17px; padding-top: 10px; line-height: 25px; }
  .info-band__company { color: var(--gold); font-weight: 700; }
  .info-band__line { display: flex; justify-content: center; align-items: center; gap: 6px; }
  .info-band__line svg { width: 15px; height: 15px; }

  .web-address { position: absolute; left: 0; right: 0; top: 352px; text-align: center; color: var(--light); font-size: 17px; letter-spacing: 4px; }
  .web-address__domain { color: var(--gold); }
</style>
</head>
<body>

<section class="card card--front" aria-label="Card front">
  <div class="brand-mark"><span class="brand-mark__square"></span><span>Harcourt Memorials</span></div>

  <div class="divider"></div>

  <div class="contacts">
    <div class="person">
      <p class="person__name">Lewis Harcourt</p>
      <p class="person__role">Director</p>
      <ul class="person__lines">
        <li class="person__line">
          <svg viewBox="0 0 16 16" aria-hidden="true"><rect x="4" y="1" width="8" height="14" rx="1.5" fill="none" stroke="#e9bd2c" stroke-width="1.4"/><line x1="7" y1="12.5" x2="9" y2="12.5" stroke="#e9bd2c" stroke-width="1.2"/></svg>
          0491630572</li>
        <li class="person__line">
          <svg viewBox="0 0 16 16" aria-hidden="true"><rect x="1" y="3.5" width="14" height="9" fill="none" stroke="#e9bd2c" stroke-width="1.4"/><polyline points="1,3.5 8,9 15,3.5" fill="none" stroke="#e9bd2c" stroke-width="1.4"/></svg>
          lewis@harcourtmemorials.com.au</li>
      </ul>
    </div>
    <div class="person">
      <p class="person__name">Simon Harcourt</p>
      <p class="person__role">Operations Manager</p>
      <ul class="person__lines">
        <li class="person__line">
          <svg viewBox="0 0 16 16" aria-hidden="true"><rect x="4" y="1" width="8" height="14" rx="1.5" fill="none" stroke="#e9bd2c" stroke-width="1.4"/><line x1="7" y1="12.5" x2="9" y2="12.5" stroke="#e9bd2c" stroke-width="1.2"/></svg>
          0417293086</li>
        <li class="person__line">
          <svg viewBox="0 0 16 16" aria-hidden="true"><rect x="1" y="3.5" width="14" height="9" fill="none" stroke="#e9bd2c" stroke-width="1.4"/><polyline points="1,3.5 8,9 15,3.5" fill="none" stroke="#e9bd2c" stroke-width="1.4"/></svg>
          simon@harcourtmemorials.com.au</li>
      </ul>
    </div>
  </div>

  <footer class="info-band">
    <p><span class="info-band__company">Harcourt Memorials:</span> Suite 17, 8 Palfrey Lane, West Carlow, Sydney NSW 2156</p>
    <p class="info-band__line">
      <svg viewBox="0 0 16 16" aria-hidden="true"><path d="M11 1 L13.5 3.5 L11.5 6 C10.5 9 8.5 11.5 6 13 L3.5 11.5 L1.5 14 C5 15.5 11 11 13.5 4 Z" fill="#e9bd2c"/></svg>
      02 9561 3048
      <svg viewBox="0 0 16 16" aria-hidden="true"><circle cx="8" cy="8" r="6.5" fill="none" stroke="#e9bd2c" stroke-width="1.3"/><ellipse cx="8" cy="8" rx="3" ry="6.5" fill="none" stroke="#e9bd2c" stroke-width="1.1"/><line x1="1.5" y1="8" x2="14.5" y2="8" stroke="#e9bd2c" stroke-width="1.1"/></svg>
      www.harcourtmemorials.com.au
    </p>
  </footer>
</section>

<section class="card card--back" aria-label="Card back">
  <div class="brand-mark"><span class="brand-mark__square"></span><span>Harcourt Memorials</span></div>
  <p class="web-address">www.<span class="web-address__domain">harcourtmemorials</span>.com.au</p>
</section>

</body>
</html>
```